Calvera fine stockings - sexy cardboard box design needed!

We need a packaging design for a new online company based in Sydney called 'Calvera Hosiery'. We will be selling sexy stockings to our customers by Italian designers. We mainly feature lace stockings, an example of which, can be seen here:
http://www.brontevassipelli.example/italy-FASHION-WINTER

The design should be a cardboard pull out box, black in colour with the logo on the cover. We are looking for the logo to communicate sophistication and sexiness.

Examples of cardboard box shapes we would like are:
http://www.tradoquel.example/product-gs/583016274/High_quality_drawer_paper_box.html

http://www.tradoquel.example/product-gs/639152487/Cardboard_drawer_box.html

29 December:
I submitted a note when I extended the deadline, but cannot see it, so will write here for clarification. It has been difficult to choose the best design as the designs submitted were of such high quality. I want to have some people judge the designs, but because of the Christmas Season I have extended the deadline so that this can be done. Thanks.

Target Market(s)

The working professional woman.

Industry/Entity Type

Fashion

Requirements
Must have
• The words "Calvera Hosiery" on the cover of the box.

The box should be a sliding drawer.

The box size should be: (22*15*2.5cm).

Washing instructions and recycling logos on the back of the box. See example of uploaded file.

Nice to have
• It would be nice to have the background of the box a dark colour, maybe charcoal? But we are open to all ideas.
Should not have
• A stock photo on cover of box.

```html
<!DOCTYPE html>
<html lang="en">
<head>
<meta charset="utf-8">
<title>Calvera Hosiery – Box Back Panel</title>
<link rel="stylesheet" href="https://fonts.googleapis.com/css2?family=Roboto+Condensed:wght@700&display=swap">
<style>
  :root {
    --cloth-light: #2c2a28;
    --cloth-dark: #171615;
    --care-tan: #8c6b50;
  }
  html, body {
    margin: 0;
    padding: 0;
    width: 819px;
    height: 1200px;
    overflow: hidden;
    background: var(--cloth-dark);
  }
  .back-panel {
    position: relative;
    width: 819px;
    height: 1200px;
    background:
      radial-gradient(ellipse at 50% 40%, rgba(255,255,255,0.04), rgba(0,0,0,0.25) 80%),
      repeating-linear-gradient(
        to bottom,
        var(--cloth-dark) 0px,
        var(--cloth-dark) 20px,
        var(--cloth-light) 20px,
        var(--cloth-light) 41px
      );
  }
  .care-symbols {
    position: absolute;
    inset: 0;
    width: 819px;
    height: 1200px;
  }
  .care-symbols .stroke {
    fill: none;
    stroke: var(--care-tan);
    stroke-width: 5;
    stroke-linejoin: round;
  }
  .care-symbols .fill {
    fill: var(--care-tan);
  }
  .care-symbols .temp {
    fill: var(--care-tan);
    font-family: "Roboto Condensed", sans-serif;
    font-weight: 700;
    font-size: 17px;
  }
</style>
</head>
<body>
  <main class="back-panel">
    <svg class="care-symbols" viewBox="0 0 900 1319" role="img" aria-label="Care instructions: wash at 30 degrees, do not bleach, do not iron, do not tumble dry, do not dry clean">
      <!-- wash 30 -->
      <g class="care-wash">
        <polyline class="stroke" points="203,607 210,607 219,655 273,655 282,607 289,607"/>
        <path class="stroke" d="M211,620 q9,-7 17,0 t17,0 t17,0 t17,0"/>
        <line class="stroke" x1="205" y1="665" x2="287" y2="665"/>
        <text class="temp" x="246" y="644" text-anchor="middle">30</text>
      </g>
      <!-- do not bleach -->
      <g class="care-bleach">
        <polygon class="fill" points="349,607 316,665 383,665"/>
        <line class="stroke" x1="313" y1="614" x2="386" y2="660"/>
        <line class="stroke" x1="386" y1="614" x2="313" y2="660"/>
      </g>
      <!-- do not iron -->
      <g class="care-iron">
        <line class="stroke" x1="425" y1="612" x2="474" y2="612"/>
        <path class="stroke" d="M413,661 Q416,632 432,630 L476,630 L479,661 Z"/>
        <line class="stroke" x1="408" y1="612" x2="481" y2="664"/>
        <line class="stroke" x1="481" y1="612" x2="408" y2="664"/>
      </g>
      <!-- do not tumble dry -->
      <g class="care-tumble">
        <rect class="stroke" x="516" y="609" width="74" height="56"/>
        <circle class="stroke" cx="553" cy="637" r="21"/>
        <line class="stroke" x1="513" y1="609" x2="593" y2="665"/>
        <line class="stroke" x1="593" y1="609" x2="513" y2="665"/>
      </g>
      <!-- do not dry clean -->
      <g class="care-dryclean">
        <circle class="stroke" cx="673" cy="637" r="29"/>
        <line class="stroke" x1="630" y1="609" x2="716" y2="665"/>
        <line class="stroke" x1="716" y1="609" x2="630" y2="665"/>
      </g>
    </svg>
  </main>
</body>
</html>
```